Basic business card

use my newly created logo - and the phrases (Lower Cost of Test & Accelarated New Product Introduction) - and my new email domain / ID - use at conferences / tradeshows

Industry/Entity Type

semiconductor

Contact Information for Business Card

Daniel K Forde, Owner, communicate via Logo - Lower COT - Cost of Test, Accelerated NPI - New Product Introduction, phone +1 555 613 0946, Chandler, Arizona, USA, daniel.forde@qal-vub.com

Font styles to use
Sans Serif

Requirements
Nice to have
• re-use my logo created via Pixel Harbor last August (#7315926)

```html
<!DOCTYPE html>
<html lang="en">
<head>
<meta charset="utf-8">
<title>QAL-VUB Business Card</title>
<link href="https://fonts.googleapis.com/css2?family=Open+Sans:wght@400;600;700&display=swap" rel="stylesheet">
<style>
  :root {
    --stage: #232323;
    --card: #1f1f22;
    --pattern: #27272a;
    --green: #6cc04a;
    --white: #f4f4f4;
    --slate: #56627e;
    --emboss-a: #2c2c30;
    --emboss-b: #141416;
  }
  * { box-sizing: border-box; margin: 0; padding: 0; }
  html, body { width: 1200px; height: 780px; overflow: hidden; }
  body {
    background: var(--stage);
    font-family: "Open Sans", Arial, sans-serif;
    display: flex;
    align-items: center;
    justify-content: center;
    gap: 34px;
  }
  .card {
    position: relative;
    width: 560px;
    height: 320px;
    background: var(--card);
    border-left: 4px solid var(--green);
    border-bottom: 4px solid var(--green);
    box-shadow: 0 18px 40px rgba(0,0,0,.55);
    overflow: hidden;
  }
  /* back side */
  .card-back .pattern-area {
    position: absolute; inset: 0;
    background: var(--pattern);
  }
  .card-back .brand {
    position: absolute; right: 34px; bottom: 74px;
  }
  .brand {
    display: flex; align-items: center; gap: 10px;
    color: var(--slate);
    font-weight: 400;
    letter-spacing: 2px;
  }
  .brand-square {
    width: 16px; height: 16px; background: var(--slate);
  }
  .card-back .brand-name { font-size: 26px; }
  /* front side */
  .card-front .brand {
    position: absolute; left: 34px; top: 60px;
  }
  .card-front .brand-square { width: 26px; height: 26px; }
  .card-front .brand-name { font-size: 40px; }
  .identity {
    position: absolute; right: 40px; top: 18px;
    text-align: right;
  }
  .identity-name { font-size: 29px; font-weight: 700; line-height: 1.1; color: var(--white); }
  .identity-name .first { color: var(--green); }
  .identity-role { font-size: 14px; color: var(--white); margin-top: 2px; }
  .accent-bar {
    position: absolute; right: 0; top: 16px;
    width: 18px; height: 52px; background: var(--green);
  }
  .address {
    position: absolute; left: 44px; top: 186px;
    color: var(--white); font-size: 14px; line-height: 1.35;
  }
  .contacts {
    position: absolute; left: 26px; bottom: 16px;
    list-style: none; color: var(--white); font-size: 14px; line-height: 1.45;
  }
  .contacts li { display: flex; align-items: center; gap: 8px; }
  .contacts svg { width: 13px; height: 13px; flex: none; }
  .mark-area {
    position: absolute; right: 20px; bottom: 22px;
    width: 250px; height: 170px;
    background: linear-gradient(140deg, var(--emboss-a), var(--emboss-b));
  }
</style>
</head>
<body>

<section class="card card-back" aria-label="Card back">
  <div class="pattern-area" role="img" aria-label="Repeating embossed brand-symbol pattern"></div>
  <div class="brand">
    <span class="brand-square"></span>
    <span class="brand-name">QAL-VUB</span>
  </div>
</section>

<section class="card card-front" aria-label="Card front">
  <div class="brand">
    <span class="brand-square"></span>
    <span class="brand-name">QAL-VUB</span>
  </div>

  <div class="identity">
    <p class="identity-name"><span class="first">Lena</span> Marovic</p>
    <p class="identity-role">Managing Director</p>
  </div>
  <span class="accent-bar"></span>

  <address class="address">
    418 Alder Ridge Rd. Suite 120<br>
    Mesa Springs, TX 70411
  </address>

  <ul class="contacts">
    <li>
      <svg viewBox="0 0 16 16"><path fill="#6cc04a" d="M3 1l3 3-1.5 2a9 9 0 0 0 5.5 5.5L12 10l3 3-2 2C7 15 1 9 1 3z"/></svg>
      (555) 204-1187
    </li>
    <li>
      <svg viewBox="0 0 16 16"><rect x="1" y="3" width="14" height="10" fill="#6cc04a"/><path d="M1 3l7 6 7-6" fill="none" stroke="#1f1f22" stroke-width="1.5"/></svg>
      info@qal-vub.com
    </li>
    <li>
      <svg viewBox="0 0 16 16"><circle cx="8" cy="8" r="7" fill="#6cc04a"/><path d="M1 8h14M8 1c-3 4-3 10 0 14M8 1c3 4 3 10 0 14" fill="none" stroke="#1f1f22" stroke-width="1"/></svg>
      www.qal-vub.com
    </li>
  </ul>

  <div class="mark-area" role="img" aria-label="Large embossed brand-symbol decoration"></div>
</section>

</body>
</html>
```